New Business Cards for NYC Salon

We are updating all of our cards. 7142-8863-2095 is my account number. We put names of our stylists on their cards. The back should include appointment space. Were looking for something more sleek and modern. Black/White Silver... or even touches of the orange color on our website which has been our thing for years. The design should communicate professional upscale boutique salon for men and women. Should be able to incorporate design into thank you cards, referral cards, brochure and postcards. The file is a zip file...we like the stacked ones black or white or the side versions.

Industry/Entity Type

Beauty Salon

Contact Information for Business Card

Marcus John's Salon313 W. 53rd Street, New York NY 10019 212-683-2741 info@marcusellingsalon.example www.marcusellingsalon.example

Font styles to use
Other font styles liked:
• trajan

Requirements
Must have
• we print a different card for every person in the salon. Begin by designing with the name Marcus. We will change it with every employee when printing. Must have a space for appointment date and time.
Nice to have
• Were looking to move towards the stacked or side placed logo but not opposed to utilizing the circular.
Should not have
• Photos

```html
<!DOCTYPE html>
<html lang="en">
<head>
<meta charset="utf-8">
<title>Marcus Elling's Salon – Business Cards</title>
<link rel="stylesheet" href="https://fonts.googleapis.com/css2?family=Cinzel:wght@400;600&display=swap">
<style>
  :root {
    --canvas: #e9e7e3;
    --card-black: #0b0b0b;
    --card-white: #f4f4f4;
    --silver: #c9c9c9;
    --grey-text: #8a8a8a;
    --ink: #111111;
    --white: #ffffff;
  }
  * { box-sizing: border-box; margin: 0; padding: 0; }
  html, body {
    width: 1200px; height: 1023px; overflow: hidden;
    background: var(--canvas);
    font-family: "Cinzel", "Times New Roman", serif;
  }
  .canvas { position: relative; width: 1200px; height: 1023px; }

  .card {
    position: absolute;
    width: 560px; height: 320px;
    background: var(--card-black);
    overflow: hidden;
    box-shadow: 0 6px 18px rgba(0,0,0,.18);
  }
  .card-front { left: 70px; top: 110px; }
  .card-back { left: 570px; top: 590px; }

  /* Front */
  .front-shape { position: absolute; inset: 0; }
  .front-info {
    position: absolute; left: 34px; top: 34px; width: 320px;
    color: var(--white);
  }
  .stylist-label {
    font-size: 13px; letter-spacing: .06em; color: var(--grey-text);
    margin-bottom: 10px;
  }
  .stylist-names { font-size: 16px; line-height: 1.35; margin-bottom: 22px; }
  .contact-list { list-style: none; font-size: 11px; line-height: 1.75; color: var(--silver); }
  .contact-list li { display: flex; align-items: center; gap: 8px; text-transform: uppercase; letter-spacing: .02em; }
  .contact-list svg { width: 12px; height: 12px; flex: none; }
  .address { margin-top: 26px; font-size: 11px; line-height: 1.45; color: var(--silver); text-transform: uppercase; }

  .front-name {
    position: absolute; right: 26px; top: 0; height: 320px; width: 150px;
    display: flex; flex-direction: column; justify-content: center; align-items: center;
    text-align: center; color: var(--ink);
    font-size: 17px; letter-spacing: .18em; line-height: 1.6;
  }

  /* Back */
  .back-name {
    position: absolute; right: 40px; top: 58px;
    text-align: right; color: var(--silver);
    font-size: 24px; letter-spacing: .28em; line-height: 1.45;
  }
  .appointment-band {
    position: absolute; left: 0; right: 0; bottom: 0; height: 86px;
    background: var(--card-white);
    border-top-left-radius: 26px;
    display: flex; align-items: center; padding: 0 26px;
    font-size: 12px; letter-spacing: .06em; color: var(--ink);
    white-space: nowrap;
  }
  .appointment-band strong { font-weight: 600; }
  .fill-line { display: inline-block; border-bottom: 1px dotted var(--ink); vertical-align: baseline; margin: 0 6px; }
  .fill-line.date { width: 120px; }
  .fill-line.time { width: 70px; }
</style>
</head>
<body>
<main class="canvas">

  <section class="card card-front" aria-label="Business card front">
    <svg class="front-shape" viewBox="0 0 560 320" aria-hidden="true">
      <rect width="560" height="320" fill="var(--card-black)"/>
      <path d="M400 0 H560 V320 H400 A210 210 0 0 1 400 0 Z" fill="var(--card-white)"/>
    </svg>

    <div class="front-info">
      <p class="stylist-label">Individualized for each stylist:</p>
      <p class="stylist-names">Marcus, Nora, Jill,<br>Lorraine, Emiliano, Helen</p>
      <ul class="contact-list">
        <li>
          <svg viewBox="0 0 12 12" aria-hidden="true"><path d="M2 1h3l1 3-2 1a7 7 0 0 0 3 3l1-2 3 1v3c-6 1-10-4-9-9z" fill="var(--silver)"/></svg>
          212-683-2741
        </li>
        <li>
          <svg viewBox="0 0 12 12" aria-hidden="true"><rect x="1" y="2.5" width="10" height="7" fill="none" stroke="var(--silver)"/><path d="M1 2.5l5 4 5-4" fill="none" stroke="var(--silver)"/></svg>
          info@marcusellingsalon.example
        </li>
        <li>
          <svg viewBox="0 0 12 12" aria-hidden="true"><circle cx="6" cy="6" r="5" fill="none" stroke="var(--silver)"/><ellipse cx="6" cy="6" rx="2.2" ry="5" fill="none" stroke="var(--silver)"/><path d="M1 6h10" stroke="var(--silver)"/></svg>
          www.marcusellingsalon.example
        </li>
      </ul>
      <p class="address">742 E. 18th Street<br>New York NY 10003</p>
    </div>

    <div class="front-name">Marcus<br>Elling's<br>Salon</div>
  </section>

  <section class="card card-back" aria-label="Business card back">
    <div class="back-name">Marcus Elling's<br>Salon</div>
    <div class="appointment-band">
      Your next&nbsp;<strong>appointment</strong>&nbsp;is on<span class="fill-line date"></span>at<span class="fill-line time"></span>AM/PM
    </div>
  </section>

</main>
</body>
</html>
```